Oriel Photography Business Card

I need a business card designed for a photography business based in Perth, Western Australia called Oriel Photography.

We specialise in wedding, event photography and portrait photography.

The business card must borrow the style of the attached logo.

The hex codes for the colours in the logo are:
#ED1D85 - Pink
#89C23E - Green
#37282F - Black

The name on the card will be:
Name: Tobrian
Phone: 0417395268
Website: www.orielphotography.example.com.au
Facebook: orielphotography

I am open and happy to accept creative concepts.

I’d like some space at the back for writing notes and appointment details.

```html
<!DOCTYPE html>
<html lang="en">
<head>
<meta charset="utf-8">
<title>Oriel Photography Business Card</title>
<link href="https://fonts.googleapis.com/css2?family=Open+Sans:ital,wght@0,400;0,700;1,400&family=Marcellus&display=swap" rel="stylesheet">
<style>
  :root {
    --pink: #ED1D85;
    --green: #89C23E;
    --black: #37282F;
    --ink: #4a4a4a;
    --grey: #6b6b6b;
    --line: #9a9a9a;
    --card: #ffffff;
    --stage: #ece9e4;
  }
  * { box-sizing: border-box; margin: 0; padding: 0; }
  html, body { width: 1200px; height: 720px; overflow: hidden; }
  body {
    background: var(--stage);
    font-family: "Open Sans", sans-serif;
    color: var(--ink);
    position: relative;
  }
  .card {
    position: absolute;
    width: 540px;
    height: 310px;
    background: var(--card);
    box-shadow: 0 4px 14px rgba(0,0,0,.12);
    overflow: hidden;
  }
  .card--front { left: 40px; top: 205px; }
  .card--back { left: 620px; top: 205px; }

  /* Front */
  .brand {
    position: absolute; left: 0; right: 0; top: 34px;
    display: flex; flex-direction: column; align-items: center; gap: 14px;
  }
  .brand__mark {
    width: 58px; height: 58px; border-radius: 50%;
    background: var(--pink);
  }
  .brand__name {
    font-size: 15px; font-weight: 400; letter-spacing: 9px;
    text-transform: uppercase; color: var(--grey);
  }
  .tab { position: absolute; width: 9px; border-radius: 6px; }
  .tab--green { right: -3px; top: 128px; height: 34px; background: var(--green); }
  .tab--pink { left: -3px; top: 208px; height: 82px; background: var(--pink); }
  .holder {
    position: absolute; right: 22px; top: 134px;
    font-size: 16px; font-weight: 700; color: var(--pink); letter-spacing: .5px;
    text-transform: uppercase;
  }
  .contacts {
    position: absolute; left: 22px; top: 212px;
    list-style: none; display: flex; flex-direction: column; gap: 7px;
    font-size: 13px; color: var(--black);
  }
  .contacts li { display: flex; align-items: center; gap: 7px; }
  .contacts svg { width: 13px; height: 13px; flex: none; }
  .dot { width: 12px; height: 12px; border-radius: 50%; background: var(--green); flex: none; }

  /* Back */
  .ghost {
    position: absolute; left: 220px; top: 80px; width: 190px; height: 190px;
    border-radius: 50%; background: var(--pink); opacity: .07;
  }
  .appt__title {
    position: absolute; left: 0; right: 0; top: 26px; text-align: center;
    font-family: "Marcellus", serif; font-size: 19px; color: var(--pink);
    letter-spacing: 1px; text-transform: uppercase;
  }
  .appt__title::after {
    content: ""; display: block; width: 300px; margin: 6px auto 0;
    border-bottom: 1px dotted var(--line);
  }
  .field { position: absolute; font-size: 14px; color: var(--ink); display: flex; align-items: center; gap: 8px; }
  .field__rule { border-bottom: 1px dotted var(--line); height: 1px; }
  .box { width: 26px; height: 20px; border: 1px solid #777; border-radius: 2px; background: #fff; }
  .box--wide { width: 120px; height: 22px; }
  .f-name { left: 40px; top: 104px; }
  .f-name .field__rule { width: 160px; }
  .f-time { left: 250px; top: 94px; }
  .f-ampm { left: 392px; top: 64px; font-size: 13px; }
  .f-time2 { left: 392px; top: 94px; }
  .f-date { left: 40px; top: 150px; }
  .f-date .field__rule { width: 110px; }
  .f-date2 { left: 240px; top: 138px; }
  .f-next { left: 70px; top: 190px; }
  .days {
    position: absolute; left: 30px; right: 30px; top: 230px;
    display: flex; flex-wrap: wrap; gap: 10px 14px; justify-content: center;
    font-size: 13px; font-weight: 700; color: var(--grey);
  }
  .day { display: flex; align-items: center; gap: 6px; }
  .note {
    position: absolute; left: 0; right: 0; bottom: 12px; text-align: center;
    font-size: 13px; font-style: italic; color: var(--grey);
  }
</style>
</head>
<body>
  <section class="card card--front" aria-label="Business card front">
    <div class="brand">
      <span class="brand__mark" aria-hidden="true"></span>
      <span class="brand__name">Oriel Photography</span>
    </div>
    <span class="tab tab--green"></span>
    <span class="holder">Tobrian</span>
    <span class="tab tab--pink"></span>
    <ul class="contacts">
      <li>
        <svg viewBox="0 0 24 24" aria-hidden="true"><circle cx="12" cy="12" r="12" fill="#89C23E"/><path d="M8 6c1-.5 2 1.8 2.3 3 .2.8-1.3 1.2-1 2 .7 1.7 1.9 2.9 3.6 3.6.8.3 1.2-1.2 2-1 1.2.3 3.5 1.3 3 2.3-.6 1.2-2 1.9-3.3 1.6C10.300 16.600 7.400 13.700 6.500 9.400 6.200 8 6.800 6.600 8 6z" fill="#fff"/></svg>
        0417395268
      </li>
      <li><span class="dot" aria-hidden="true"></span>orielphotography</li>
      <li><span class="dot" aria-hidden="true"></span>www.orielphotography.example.com.au</li>
    </ul>
  </section>

  <section class="card card--back" aria-label="Business card back">
    <span class="ghost" aria-hidden="true"></span>
    <h2 class="appt__title">Your Appointment</h2>
    <div class="field f-ampm">am / pm</div>
    <div class="field f-name">Name : <span class="field__rule"></span></div>
    <div class="field f-time">Time :</div>
    <div class="field f-time2"><span class="box box--wide"></span></div>
    <div class="field f-date">Date : <span class="field__rule"></span></div>
    <div class="field f-date2"><span class="box box--wide"></span></div>
    <div class="field f-next">Next Appointment</div>
    <div class="days">
      <span class="day">MON <span class="box"></span></span>
      <span class="day">TUE <span class="box"></span></span>
      <span class="day">WED <span class="box"></span></span>
      <span class="day">THU <span class="box"></span></span>
      <span class="day">FRI <span class="box"></span></span>
      <span class="day">SAT <span class="box"></span></span>
    </div>
    <p class="note">We appreciate a 24 hr. notice for cancellations</p>
  </section>
</body>
</html>
```